Harbor Law Stationary - Law Firm

I am looking for a designer who can help me design letterhead and envelopes consistent with our new business cards. Feel free to reach out to me directly at ned@harborlawgroup.example. Thank you!! Visit harborlawgroup.example to see our site and the attached files for creative assets.

Target Market(s)

Anyone needing a lawyer

Font styles to use
Other font styles liked:
• Adobe Caslon Pro

Requirements
Must have
• Adobe Caslon Pro font
Full color
Nice to have
• My photo on front along with 2/3 face of camo - see mock up for example of what I have in mind.

American colors - similar to the ones found on my website and gold.

```html
<!DOCTYPE html>
<html lang="en">
<head>
<meta charset="utf-8">
<title>Harbor Law — Envelope Set</title>
<link href="https://fonts.googleapis.com/css2?family=Libre+Caslon+Text:wght@400;700&display=swap" rel="stylesheet">
<style>
  :root {
    --navy: #021d3f;
    --navy-flap: #03214b;
    --gold: #a89556;
    --white: #ffffff;
    --ghost: #3c4452;
    --backdrop: #eeeeee;
    --serif: "Libre Caslon Text", "Times New Roman", serif;
  }
  * { margin: 0; padding: 0; box-sizing: border-box; }
  html, body {
    width: 1200px; height: 800px; overflow: hidden;
    background: var(--backdrop);
    font-family: var(--serif);
  }
  .stage { position: relative; width: 1200px; height: 800px; }
  .envelope {
    position: absolute; left: 270px; width: 660px; height: 287px;
    background: var(--navy);
    box-shadow: 0 2px 6px rgba(0,0,0,0.18);
    overflow: hidden;
  }
  .envelope--back { top: 58px; }
  .envelope--front { top: 430px; }

  .flap { position: absolute; top: 0; left: 0; width: 660px; height: 96px; }
  .mission {
    position: absolute; top: 30px; left: 0; right: 0;
    text-align: center; color: var(--white);
    font-size: 19px; letter-spacing: 0.02em;
  }

  .brand {
    position: absolute; left: 52px; top: 48px;
    color: var(--gold); font-weight: 700;
    font-size: 26px; line-height: 1.05; letter-spacing: 0.12em;
    text-transform: uppercase;
  }
  .return-address {
    position: absolute; left: 52px; top: 170px;
    color: var(--white); font-size: 13.5px; line-height: 1.35;
    font-style: normal;
  }
  .brand-watermark {
    position: absolute; right: 40px; bottom: 34px;
    color: var(--ghost); font-size: 30px; font-weight: 700;
    letter-spacing: 0.12em; text-transform: uppercase;
    line-height: 1.05; text-align: right;
  }
</style>
</head>
<body>
<main class="stage">
  <section class="envelope envelope--back" aria-label="Envelope back">
    <svg class="flap" viewBox="0 0 660 96" aria-hidden="true">
      <path d="M0 0 H660 V6 L628 74 Q622 84 608 86 L52 86 Q38 84 32 74 L0 6 Z" fill="var(--navy-flap)"/>
      <path d="M60 87 L600 87" fill="none" stroke="var(--gold)" stroke-width="1"/>
    </svg>
    <p class="mission">Our Mission: Steady Counsel, Every Step</p>
  </section>

  <section class="envelope envelope--front" aria-label="Envelope front">
    <h1 class="brand">Harbor<br>Law</h1>
    <address class="return-address">
      214 Anchor Row<br>
      Bayport, FL 34001<br>
      (555) 014-2291<br>
      mara@harborlawgroup.example<br>
      www.harborlawgroup.example
    </address>
    <p class="brand-watermark" aria-hidden="true">Harbor<br>Law</p>
  </section>
</main>
</body>
</html>
```